Agriculture farming Hemp and CBD

The logo is in works with your company now, should be ready in a few days. We have our Domain (kestrelbrookhollow.com) We would like to see incorporated seed to growth, but not necessary. we would like to nature colors and some black and green. we have our farm and will be growing and selling HEMP and CBD we are based in the state of Virginia. Would like to incorporate the words pause, play, rewind if possible but not necessary.

Target Market(s)

20 years old to elderly

Coding

Coded - Design and coding required

Number of Pages Required

3 page

Font styles to use
Serif

Requirements
Must have
• I'm not sure on the must haves, we are open to any ideas, we would definitely like to see Hemp and CBD included, may the life cycle of seed to plant. We must have a pop up asking if you are 20 years old before they can enter our site and to view or purchase our product. I want the design to be totally different than what i uploaded.
Nice to have
• Would like to see natural colors as well as black and green
Should not have
• I want

```html
<!DOCTYPE html>
<html lang="en">
<head>
<meta charset="utf-8">
<title>Kestrel Brook Hollow – Hemp &amp; CBD</title>
<link href="https://fonts.googleapis.com/css2?family=Rubik:wght@400;500&family=Lato:ital,wght@0,400;0,700;1,400&display=swap" rel="stylesheet">
<style>
:root{
  --green:#00d615;
  --black:#000;
  --ink:#111;
  --white:#fff;
  --grey-bg:#a5a5a5;
  --muted:#666;
  --overlay:rgba(0,0,0,.72);
  --hero-tones:linear-gradient(100deg,#142a10 0%,#21421a 30%,#2f5a22 50%,#4d6a26 64%,#9c8422 76%,#c8a52a 82%,#5a7428 90%,#2c4a1c 100%);
  --jar-tones:linear-gradient(180deg,#eef0ea 0%,#d8dccf 18%,#c8a82a 34%,#b59414 56%,#8a7a2a 68%,#3c44c0 82%,#2a2e8e 100%);
  --reviews-tones:linear-gradient(100deg,#0c150a 0%,#16220f 40%,#23301a 62%,#3d3c17 80%,#2a2a12 92%,#141a0c 100%);
}
*{margin:0;padding:0;box-sizing:border-box}
html,body{width:942px;height:1200px;overflow:hidden;background:var(--grey-bg)}
.board{position:absolute;left:0;top:0;width:1708px;height:2175px;transform:scale(.5515);transform-origin:0 0;background:var(--grey-bg)}
.page{position:absolute;top:104px;width:669px;height:1966px;background:var(--black);overflow:hidden;font-family:"Lato",sans-serif;color:var(--white)}
.page--gate{left:161px}
.page--open{left:878px}
.abs{position:absolute}
.heading{font-family:"Rubik",sans-serif;font-weight:500;text-transform:uppercase;letter-spacing:.2px}
.accent{color:var(--green)}

.topbar{left:0;top:0;width:669px;height:24px;background:var(--green);font-size:7.5px;font-weight:700}
.topbar .social{left:80px;top:8px;display:flex;gap:5px}
.dot{width:7px;height:7px;border-radius:50%;background:var(--white)}
.topbar .contact{right:81px;top:7px;display:flex;gap:8px;align-items:center}
.ic-phone{display:inline-block;width:6px;height:6px;border:1.5px solid var(--white);border-radius:1px 3px 1px 3px;margin-right:3px;vertical-align:-1px}

.hero-photo{left:0;top:24px;width:669px;height:396px;background:var(--hero-tones)}
.logo{left:80px;top:38px;font-size:21px;font-weight:500;font-family:"Rubik",sans-serif;letter-spacing:-.2px}
.logo .mark{display:inline-block;width:8px;height:8px;border-radius:50%;background:var(--green);margin-left:3px;vertical-align:3px}
.nav{left:288px;top:50px;display:flex;gap:13px;font-size:7.5px;font-weight:700;text-transform:uppercase}
.nav .current{border-bottom:2px solid var(--green);padding-bottom:3px}
.login{left:509px;top:44px;width:50px;height:22px;border-radius:11px;background:var(--green);font-size:8px;font-weight:700;text-align:center;line-height:22px}
.cart{left:567px;top:47px}
.hero-title{left:80px;top:140px;font-family:"Rubik",sans-serif;font-weight:500;font-size:34px;letter-spacing:-.3px}
.hero-sub{left:81px;top:198px;font-size:13px;font-weight:700}
.btn{border-radius:16px;background:var(--green);color:var(--white);font-weight:700;text-transform:uppercase;text-align:center}
.shop{left:81px;top:241px;width:112px;height:31px;line-height:31px;font-size:10.5px}
.dots{left:81px;top:314px;display:flex;gap:4px}
.dots span{width:6px;height:6px;border-radius:50%;background:var(--white)}
.dots span.ring{background:none;border:1.5px solid var(--white)}

.about-photo{left:91px;top:461px;width:226px;height:226px;border-radius:50%;background:var(--jar-tones)}
.about-title{left:340px;top:462px;font-size:26px;line-height:29px}
.about-name{left:340px;top:493px;font-family:"Rubik",sans-serif;font-weight:500;font-size:26px}
.about-copy{left:340px;top:540px;width:252px;font-size:8.2px;line-height:14.7px}
.more{left:340px;top:648px;width:86px;height:24px;line-height:24px;font-size:8px}

.section-title{left:0;width:669px;text-align:center;font-size:26px}
.products{left:80px;top:862px;display:flex;gap:9px}
.product{width:120px;height:157px;border:2px solid var(--white);text-align:center;position:relative}
.product .shot{margin:3px;height:80px}
.product .name{font-size:10px;font-weight:700;margin-top:8px}
.product .price{font-size:10px;font-weight:700;margin-top:5px}
.product .add{display:inline-block;margin-top:6px;width:58px;height:19px;line-height:19px;border-radius:10px;background:var(--ink);font-size:6px;font-weight:700}
.arrow{width:24px;height:24px;border-radius:50%;border:1.5px solid var(--white)}

.posts{left:86px;top:1222px;display:flex;gap:15px}
.post{width:156px;height:192px;background:var(--white);color:var(--ink);position:relative}
.post .shot{height:90px}
.post .date{position:absolute;left:12px;top:100px;width:24px;height:24px;background:var(--green);color:var(--white);font-size:8px;font-weight:700;text-align:center;line-height:9px;padding-top:3px}
.post .date.dark{background:var(--ink)}
.post .date small{display:block;font-size:6.5px}
.post .title{position:absolute;left:46px;top:100px;font-size:8px;line-height:12px;font-weight:700}
.post .body{position:absolute;left:12px;top:134px;width:134px;font-size:6.2px;line-height:9.5px;color:var(--muted)}
.post .link{position:absolute;left:12px;top:168px;font-size:6.2px;font-weight:700;color:var(--green)}

.reviews-photo{left:0;top:1505px;width:669px;height:285px;background:var(--reviews-tones)}
.avatar{left:125px;top:1622px;width:64px;height:64px;border-radius:50%;border:3px solid var(--green);background:linear-gradient(135deg,#e6e2dc 0%,#d8b49a 40%,#8a5a40 75%,#3a2618 100%)}
.quote{left:209px;top:1617px;width:340px;font-size:9px;font-style:italic;line-height:17.5px}
.author{left:209px;top:1700px;font-size:9px;font-weight:700}
.author em{font-weight:400}
.stars{color:var(--green);font-size:12px;letter-spacing:3px;margin-left:3px;font-style:normal}

.news-title{left:80px;top:1862px;font-size:12.5px;font-weight:700;text-transform:uppercase}
.news-form{left:80px;top:1896px;width:175px;height:26px;border-radius:13px;background:var(--white);border:2px solid var(--green)}
.news-form span{position:absolute;left:16px;top:7px;font-size:6.5px;color:#999}
.news-form b{position:absolute;right:0;top:0;width:70px;height:22px;line-height:22px;border-radius:11px;background:var(--green);color:var(--white);font-size:9px;text-align:center}
.foot-nav{left:312px;top:1860px;display:flex;gap:16px;font-size:10px;font-weight:700;text-transform:uppercase}
.copyright{left:312px;top:1885px;font-size:7.5px}
.foot-social{left:312px;top:1914px;display:flex;gap:6px}
.cards{left:382px;top:1913px;display:flex;gap:5px}
.cards span{width:17px;height:12px;border-radius:2px;background:#c9c9c9}

.shade{left:0;top:0;width:669px;height:1966px;background:var(--overlay)}
.gate{left:124px;top:169px;width:422px;height:166px;background:var(--white);border:2px solid var(--green);color:var(--black);text-align:center}
.gate h2{font-family:"Rubik",sans-serif;font-weight:400;font-size:19px;margin-top:26px;letter-spacing:.2px}
.gate p{font-size:10px;margin-top:14px}
.gate .actions{display:flex;gap:7px;justify-content:center;margin-top:20px}
.gate .actions span{width:84px;height:32px;line-height:32px;border-radius:16px;font-size:11px;font-weight:700;color:var(--white)}
.gate .enter{background:var(--green)}
.gate .exit{background:var(--ink)}
.close{left:518px;top:168px;width:30px;height:30px;border-radius:50%;background:var(--green);border:2px solid var(--white)}
</style>
</head>
<body>
<div class="board">

<!-- Page variant with age gate -->
<section class="page page--gate">
  <div class="abs hero-photo" role="img" aria-label="Hemp leaves and a dropper bottle of CBD oil beside a wooden spoon of seeds"></div>
  <svg class="abs" style="left:0;top:0" width="669" height="1966" viewBox="0 0 669 1966">
    <path d="M0,318 Q335,500 669,318 L669,425 L0,425 Z" fill="#000"/>
    <path d="M30,330 Q335,500 669,312" fill="none" stroke="#00d615" stroke-width="4"/>
    <path d="M230,453 A124,124 0 1,0 230,695" fill="none" stroke="#00d615" stroke-width="5"/>
    <path d="M0,775 Q335,705 669,775 L669,1078 Q335,1145 0,1078 Z" fill="#00d615"/>
  </svg>
  <div class="abs reviews-photo" role="img" aria-label="Dark backdrop of CBD oil pouring from a spoon"></div>
  <svg class="abs" style="left:0;top:1490px" width="669" height="340" viewBox="0 0 669 340">
    <path d="M0,31 L0,0 L669,0 L669,31 Q335,-40 0,31 Z" fill="#000"/>
    <path d="M0,31 Q335,-40 669,31" fill="none" stroke="#00d615" stroke-width="3"/>
    <path d="M0,290 Q335,355 669,290 L669,340 L0,340 Z" fill="#000"/>
    <path d="M0,290 Q335,355 669,290" fill="none" stroke="#00d615" stroke-width="3"/>
  </svg>

  <div class="abs topbar">
    <div class="abs social"><span class="dot"></span><span class="dot"></span><span class="dot"></span></div>
    <div class="abs contact"><span><i class="ic-phone"></i>1 555 010 0142</span><span>|</span><span>Email : info@kestrelbrookhollow.com</span></div>
  </div>
  <div class="abs logo">kestrelbrookhollow<span class="mark"></span></div>
  <nav class="abs nav"><span class="current">Home</span><span>About us</span><span>Products</span><span>News</span><span>Contact</span></nav>
  <div class="abs btn login">LOGIN</div>
  <svg class="abs cart" width="22" height="18" viewBox="0 0 22 18"><path d="M1,2 H5 L8,12 H18 L20,5 H6" fill="none" stroke="#fff" stroke-width="2"/><circle cx="9" cy="15.5" r="1.6" fill="#fff"/><circle cx="17" cy="15.5" r="1.6" fill="#fff"/></svg>
  <h1 class="abs hero-title">Pause,<span class="accent">Play</span>,Rewind</h1>
  <p class="abs hero-sub">We do Agriculture farming Hemp and CBD</p>
  <div class="abs btn shop">Shop now</div>
  <div class="abs dots"><span></span><span></span><span class="ring"></span><span></span><span></span></div>

  <div class="abs about-photo" role="img" aria-label="Gloved hands holding a glass jar of CBD oil"></div>
  <h2 class="abs heading about-title">About</h2>
  <p class="abs about-name">kestrel <span class="accent">brook</span> hollow</p>
  <p class="abs about-copy">Sed ut perspiciatis unde omnis iste natus error sit voluptatecusantium doloremque laudantium, totam rem aperiam, eaque ipsa quae ab illo inventore veritatis et quasi architecto beatae vitae dicta sunt explicabo. Nemo enim ipsam voluptatem quia voluptas sit aspernatur aut odit aut fugit, sed quia consequuntur magni dolores eos qui ratione voluptatem sequi n porro quisquam est, qui dolorem ipsum quia dolor sit amet,</p>
  <div class="abs btn more">Read more</div>

  <h2 class="abs heading section-title" style="top:800px">Featured products</h2>
  <div class="abs arrow" style="left:43px;top:928px"></div>
  <div class="abs arrow" style="left:602px;top:928px"></div>
  <div class="abs products">
    <div class="product"><div class="shot" role="img" aria-label="Oil bottles with hemp seeds" style="background:linear-gradient(160deg,#d8d9c4 0%,#9aa24a 40%,#6f7a30 70%,#4a4a2a 100%)"></div><div class="name">Product Name</div><div class="price">$57.97</div><span class="add">ADD TO CART</span></div>
    <div class="product"><div class="shot" role="img" aria-label="Dropper bottle and cream jar with hemp leaf" style="background:linear-gradient(160deg,#fafaf7 0%,#ecece6 45%,#c8cfc0 75%,#7a9a5a 100%)"></div><div class="name">Product Name</div><div class="price">$57.97</div><span class="add">ADD TO CART</span></div>
    <div class="product"><div class="shot" role="img" aria-label="Sack of hemp seeds and oil bottle on wood" style="background:linear-gradient(160deg,#cdb98a 0%,#b59a4a 40%,#7c6a3c 70%,#4a3e2a 100%)"></div><div class="name">Product Name</div><div class="price">$57.97</div><span class="add">ADD TO CART</span></div>
    <div class="product"><div class="shot" role="img" aria-label="Small CBD bottle among hemp leaves" style="background:linear-gradient(160deg,#b8c0b4 0%,#7a9464 40%,#3f6a2c 70%,#2a3e22 100%)"></div><div class="name">Product Name</div><div class="price">$57.97</div><span class="add">ADD TO CART</span></div>
  </div>

  <h2 class="abs heading section-title" style="top:1163px">Blog P<span class="accent">o</span>sts</h2>
  <div class="abs posts">
    <div class="post"><div class="shot" role="img" aria-label="Hand holding a drop of oil near hemp leaves" style="background:linear-gradient(135deg,#e8c8aa,#d2a684 60%,#b78a66)"></div><div class="date">02<small>JAN</small></div><div class="title">Pellentesque faucibus<br>Ut accumsan ultric</div><p class="body">Duis quam Nam eget lacus Aliquam erat volutpat Quisque dignissim congue leo Mauris vel lacus vitae felis vestibulum</p><span class="link">READ MORE</span></div>
    <div class="post"><div class="shot" role="img" aria-label="Oil dropper in front of hemp plants" style="background:linear-gradient(135deg,#dfe4d2,#a9bb8a 50%,#5f7e40)"></div><div class="date dark">02<small>JAN</small></div><div class="title">Pellentesque faucibus<br>Ut accumsan ultric</div><p class="body">Duis quam Nam eget lacus Aliquam erat volutpat Quisque dignissim congue leo Mauris vel lacus vitae felis vestibulum</p><span class="link">READ MORE</span></div>
    <div class="post"><div class="shot" role="img" aria-label="Man examining a bottle of CBD oil" style="background:linear-gradient(135deg,#b4b2aa,#7a7a74 50%,#3a4654)"></div><div class="date">02<small>JAN</small></div><div class="title">Pellentesque faucibus<br>Ut accumsan ultric</div><p class="body">Duis quam Nam eget lacus Aliquam erat volutpat Quisque dignissim congue leo Mauris vel lacus vitae felis vestibulum</p><span class="link">READ MORE</span></div>
  </div>

  <h2 class="abs heading section-title" style="top:1552px">Client <span class="accent">Reviews</span></h2>
  <div class="abs arrow" style="left:80px;top:1643px"></div>
  <div class="abs arrow" style="left:564px;top:1643px"></div>
  <div class="abs avatar" role="img" aria-label="Customer portrait"></div>
  <p class="abs quote">Lorem ipsum dolor sit amet, consectetur adipiscing elit, sed do eiusmod tincididunt ut labore et dolore magna aliqsum suspendisse ultricesus commodo viveraecenas accumsan lacus vel facilisorem ipsum dolor sit amconsectetur adipiscing elit, sed do eiusmod tempor incididunt.</p>
  <p class="abs author">- MARA ELLISON,<em>Customer</em><span class="stars">★★★★★</span></p>

  <p class="abs news-title">Sign up newsletter</p>
  <div class="abs news-form"><span>Enter Email</span><b>SIGN UP</b></div>
  <nav class="abs foot-nav"><span>Home</span><span>About us</span><span>Products</span><span>News</span><span>Contact</span></nav>
  <p class="abs copyright">© 2020 Kestrel Brook Hollow.All Rights reserved | Privacy Policy</p>
  <div class="abs foot-social"><span class="dot"></span><span class="dot"></span><span class="dot"></span></div>
  <div class="abs cards"><span></span><span></span><span></span><span></span><span></span></div>

  <div class="abs shade"></div>
  <div class="abs gate">
    <h2>YOU MUST BE 21 <span class="accent">OR</span> OLDER TO ENTER!</h2>
    <p>Our content is Age Restricted for guests above 21 years old</p>
    <div class="actions"><span class="enter">ENTER</span><span class="exit">EXIT</span></div>
  </div>
  <div class="abs close"><svg width="26" height="26" viewBox="0 0 26 26"><path d="M9,9 L17,17 M17,9 L9,17" stroke="#fff" stroke-width="2.6" stroke-linecap="round"/></svg></div>
</section>

<!-- Page variant without age gate -->
<section class="page page--open">
  <div class="abs hero-photo" role="img" aria-label="Hemp leaves and a dropper bottle of CBD oil beside a wooden spoon of seeds"></div>
  <svg class="abs" style="left:0;top:0" width="669" height="1966" viewBox="0 0 669 1966">
    <path d="M0,318 Q335,500 669,318 L669,425 L0,425 Z" fill="#000"/>
    <path d="M30,330 Q335,500 669,312" fill="none" stroke="#00d615" stroke-width="4"/>
    <path d="M230,453 A124,124 0 1,0 230,695" fill="none" stroke="#00d615" stroke-width="5"/>
    <path d="M0,775 Q335,705 669,775 L669,1078 Q335,1145 0,1078 Z" fill="#00d615"/>
  </svg>
  <div class="abs reviews-photo" role="img" aria-label="Dark backdrop of CBD oil pouring from a spoon"></div>
  <svg class="abs" style="left:0;top:1490px" width="669" height="340" viewBox="0 0 669 340">
    <path d="M0,31 L0,0 L669,0 L669,31 Q335,-40 0,31 Z" fill="#000"/>
    <path d="M0,31 Q335,-40 669,31" fill="none" stroke="#00d615" stroke-width="3"/>
    <path d="M0,290 Q335,355 669,290 L669,340 L0,340 Z" fill="#000"/>
    <path d="M0,290 Q335,355 669,290" fill="none" stroke="#00d615" stroke-width="3"/>
  </svg>

  <div class="abs topbar">
    <div class="abs social"><span class="dot"></span><span class="dot"></span><span class="dot"></span></div>
    <div class="abs contact"><span><i class="ic-phone"></i>1 555 010 0142</span><span>|</span><span>Email : info@kestrelbrookhollow.com</span></div>
  </div>
  <div class="abs logo">kestrelbrookhollow<span class="mark"></span></div>
  <nav class="abs nav"><span class="current">Home</span><span>About us</span><span>Products</span><span>News</span><span>Contact</span></nav>
  <div class="abs btn login">LOGIN</div>
  <svg class="abs cart" width="22" height="18" viewBox="0 0 22 18"><path d="M1,2 H5 L8,12 H18 L20,5 H6" fill="none" stroke="#fff" stroke-width="2"/><circle cx="9" cy="15.5" r="1.6" fill="#fff"/><circle cx="17" cy="15.5" r="1.6" fill="#fff"/></svg>
  <h1 class="abs hero-title">Pause,<span class="accent">Play</span>,Rewind</h1>
  <p class="abs hero-sub">We do Agriculture farming Hemp and CBD</p>
  <div class="abs btn shop">Shop now</div>
  <div class="abs dots"><span></span><span></span><span class="ring"></span><span></span><span></span></div>

  <div class="abs about-photo" role="img" aria-label="Gloved hands holding a glass jar of CBD oil"></div>
  <h2 class="abs heading about-title">About</h2>
  <p class="abs about-name">kestrel <span class="accent">brook</span> hollow</p>
  <p class="abs about-copy">Sed ut perspiciatis unde omnis iste natus error sit voluptatecusantium doloremque laudantium, totam rem aperiam, eaque ipsa quae ab illo inventore veritatis et quasi architecto beatae vitae dicta sunt explicabo. Nemo enim ipsam voluptatem quia voluptas sit aspernatur aut odit aut fugit, sed quia consequuntur magni dolores eos qui ratione voluptatem sequi n porro quisquam est, qui dolorem ipsum quia dolor sit amet,</p>
  <div class="abs btn more">Read more</div>

  <h2 class="abs heading section-title" style="top:800px">Featured products</h2>
  <div class="abs arrow" style="left:43px;top:928px"></div>
  <div class="abs arrow" style="left:602px;top:928px"></div>
  <div class="abs products">
    <div class="product"><div class="shot" role="img" aria-label="Oil bottles with hemp seeds" style="background:linear-gradient(160deg,#d8d9c4 0%,#9aa24a 40%,#6f7a30 70%,#4a4a2a 100%)"></div><div class="name">Product Name</div><div class="price">$57.97</div><span class="add">ADD TO CART</span></div>
    <div class="product"><div class="shot" role="img" aria-label="Dropper bottle and cream jar with hemp leaf" style="background:linear-gradient(160deg,#fafaf7 0%,#ecece6 45%,#c8cfc0 75%,#7a9a5a 100%)"></div><div class="name">Product Name</div><div class="price">$57.97</div><span class="add">ADD TO CART</span></div>
    <div class="product"><div class="shot" role="img" aria-label="Sack of hemp seeds and oil bottle on wood" style="background:linear-gradient(160deg,#cdb98a 0%,#b59a4a 40%,#7c6a3c 70%,#4a3e2a 100%)"></div><div class="name">Product Name</div><div class="price">$57.97</div><span class="add">ADD TO CART</span></div>
    <div class="product"><div class="shot" role="img" aria-label="Small CBD bottle among hemp leaves" style="background:linear-gradient(160deg,#b8c0b4 0%,#7a9464 40%,#3f6a2c 70%,#2a3e22 100%)"></div><div class="name">Product Name</div><div class="price">$57.97</div><span class="add">ADD TO CART</span></div>
  </div>

  <h2 class="abs heading section-title" style="top:1163px">Blog P<span class="accent">o</span>sts</h2>
  <div class="abs posts">
    <div class="post"><div class="shot" role="img" aria-label="Hand holding a drop of oil near hemp leaves" style="background:linear-gradient(135deg,#e8c8aa,#d2a684 60%,#b78a66)"></div><div class="date">02<small>JAN</small></div><div class="title">Pellentesque faucibus<br>Ut accumsan ultric</div><p class="body">Duis quam Nam eget lacus Aliquam erat volutpat Quisque dignissim congue leo Mauris vel lacus vitae felis vestibulum</p><span class="link">READ MORE</span></div>
    <div class="post"><div class="shot" role="img" aria-label="Oil dropper in front of hemp plants" style="background:linear-gradient(135deg,#dfe4d2,#a9bb8a 50%,#5f7e40)"></div><div class="date dark">02<small>JAN</small></div><div class="title">Pellentesque faucibus<br>Ut accumsan ultric</div><p class="body">Duis quam Nam eget lacus Aliquam erat volutpat Quisque dignissim congue leo Mauris vel lacus vitae felis vestibulum</p><span class="link">READ MORE</span></div>
    <div class="post"><div class="shot" role="img" aria-label="Man examining a bottle of CBD oil" style="background:linear-gradient(135deg,#b4b2aa,#7a7a74 50%,#3a4654)"></div><div class="date">02<small>JAN</small></div><div class="title">Pellentesque faucibus<br>Ut accumsan ultric</div><p class="body">Duis quam Nam eget lacus Aliquam erat volutpat Quisque dignissim congue leo Mauris vel lacus vitae felis vestibulum</p><span class="link">READ MORE</span></div>
  </div>

  <h2 class="abs heading section-title" style="top:1552px">Client <span class="accent">Reviews</span></h2>
  <div class="abs arrow" style="left:80px;top:1643px"></div>
  <div class="abs arrow" style="left:564px;top:1643px"></div>
  <div class="abs avatar" role="img" aria-label="Customer portrait"></div>
  <p class="abs quote">Lorem ipsum dolor sit amet, consectetur adipiscing elit, sed do eiusmod tincididunt ut labore et dolore magna aliqsum suspendisse ultricesus commodo viveraecenas accumsan lacus vel facilisorem ipsum dolor sit amconsectetur adipiscing elit, sed do eiusmod tempor incididunt.</p>
  <p class="abs author">- MARA ELLISON,<em>Customer</em><span class="stars">★★★★★</span></p>

  <p class="abs news-title">Sign up newsletter</p>
  <div class="abs news-form"><span>Enter Email</span><b>SIGN UP</b></div>
  <nav class="abs foot-nav"><span>Home</span><span>About us</span><span>Products</span><span>News</span><span>Contact</span></nav>
  <p class="abs copyright">© 2020 Kestrel Brook Hollow.All Rights reserved | Privacy Policy</p>
  <div class="abs foot-social"><span class="dot"></span><span class="dot"></span><span class="dot"></span></div>
  <div class="abs cards"><span></span><span></span><span></span><span></span><span></span></div>
</section>

</div>
</body>
</html>
```